Business Intelligence Application - Reporting Menu and Report Criteria Design

Looking for a fresh, effective and user friendly view for the menu structure and reporting criteria screen format for a business reporting application. Initial format completed, content structure is in place, but we need the 'wow' design.. as its a serious professional report/BI tool it has to fall within certain guidelines for clarity and graphics..but we want it to be slick, friendly, great user experience. There is a large amount of complex content to fit into a small space and we need it to be very inviting, modern and intuitive.. If interested, please review the attachment. We have live screens in operation, but feel these could be improved and looking forward to seeing what great creative suggestions could be made. Please review work done to date in the attached.. We are not looking for a total re-design of everything, all the basic business content/structure is there.. but tell us what we could do to improve this in terms of graphic design... particularly the criteria screens.. thanks!
Updates

Reason: Need a few more days to review designs - thanks for all submissions so far, we will make a selection shortly.

Target Market(s)

Business analysts, hotel operations teams, finance analysts hospitality industry

Industry/Entity Type

Hospitality

Coding

Coded - Design and coding required

Number of Pages Required

4 page

Font styles to use
Sans Serif
Other font styles liked:
• Candara, please see example in deck

Colors
3276b5
3176b5
0255a3
85acd3
33a6d7
cee9f5
85cae6

Requirements
Must have
• sharp clear, logical menu structure, (currently it has 'clicks to sub-menus, we need hover over, slide to sub-menus..) colour, styling.. and most focus on revision of criteria.. right now is somewhat heavy, cumbersome.. keep colour and friendly intuitive process steps.. its heavy analytical stuff.. best of luck!
Should not have
• No grey fonts on white or grey screens! many business apps are not readable or sharp.. or fonts are too small.. colourless, so please avoid that.. see our deck - sharp dark (navy) or black fonts on white, or light shading..

```html
<!DOCTYPE html>
<html lang="en">
<head>
<meta charset="utf-8">
<title>Yieldora – Report Criteria</title>
<link rel="stylesheet" href="https://fonts.googleapis.com/css2?family=Open+Sans:wght@400;600;700&display=swap">
<style>
  :root {
    --navy: #0255a3;
    --blue: #3276b5;
    --blue-mid: #3a7dbf;
    --blue-light: #4286c7;
    --blue-hover: #4a8ccb;
    --page: #ececec;
    --white: #ffffff;
    --ink: #1c2a3a;
    --line: #9aa3ad;
  }
  * { box-sizing: border-box; margin: 0; padding: 0; }
  html, body { width: 1200px; height: 666px; overflow: hidden; }
  body {
    position: relative;
    font-family: "Open Sans", Candara, sans-serif;
    background: var(--page);
    color: var(--ink);
  }

  /* Top bar */
  .topbar {
    position: absolute; left: 0; top: 0; width: 1200px; height: 48px;
    background: var(--navy); color: var(--white);
  }
  .brand { position: absolute; left: 27px; top: 12px; display: flex; align-items: center; gap: 8px; }
  .brand-dot { width: 20px; height: 20px; border-radius: 50%; background: #33a6d7; }
  .brand-name { font-size: 16px; font-weight: 400; }
  .nav-item {
    position: absolute; top: 0; height: 48px; line-height: 48px;
    font-size: 11px; color: var(--white); letter-spacing: .2px;
  }
  .nav-item.is-open { background: var(--blue); padding: 0 15px; left: 244px; width: 70px; line-height: 46px; }
  .caret { display: inline-block; vertical-align: middle; margin-left: 4px; }
  .date { position: absolute; left: 936px; top: 10px; font-size: 10px; line-height: 14px; font-weight: 600; }
  .date span { display: block; font-weight: 400; font-size: 9px; padding-left: 1px; }
  .avatar { position: absolute; left: 1040px; top: 9px; width: 28px; height: 28px; border-radius: 50%; background: #d9d9d9; }
  .welcome { position: absolute; left: 1075px; top: 12px; font-size: 9px; line-height: 11px; }
  .welcome strong { display: block; font-size: 11px; font-weight: 700; letter-spacing: .3px; }
  .icon { position: absolute; top: 15px; }

  /* Criteria card */
  .criteria {
    position: absolute; left: 214px; top: 152px; width: 440px; height: 379px;
    background: var(--white); box-shadow: 0 2px 10px rgba(0,0,0,.08);
  }
  .field {
    position: absolute; left: 18px; width: 404px; height: 42px;
    border: 1px solid var(--line); background: var(--white);
    font-size: 10px; line-height: 40px; padding-left: 21px; color: var(--ink);
  }
  .field .arrow { position: absolute; right: 16px; top: 17px; }

  /* Property panel */
  .property {
    position: absolute; left: 654px; top: 152px; width: 297px; height: 379px;
    background: var(--white); box-shadow: 0 2px 10px rgba(0,0,0,.08);
  }
  .property-head {
    height: 40px; background: var(--navy); color: var(--white);
    font-size: 11px; font-weight: 600; line-height: 40px; padding-left: 23px;
  }
  .property-item { text-align: center; }
  .property-item.first { height: 138px; padding-top: 50px; border-bottom: 1px solid #e3e3e3; }
  .property-item.second { padding-top: 29px; }
  .property-name { font-size: 11.5px; color: var(--ink); }
  .property-code { font-size: 19px; color: var(--navy); margin-top: 6px; letter-spacing: .5px; }

  /* Admin menu */
  .menu {
    position: absolute; left: 244px; top: 48px; width: 178px; height: 168px;
    background: var(--blue-mid);
  }
  .menu-item {
    position: absolute; left: 0; width: 178px; height: 30px; line-height: 30px;
    padding-left: 27px; font-size: 12px; color: var(--white);
  }
  .menu-item.is-active { background: var(--blue-hover); left: -1px; width: 179px; }
  .submenu {
    position: absolute; left: 420px; top: 133px; width: 178px; height: 261px;
    background: var(--blue-light); box-shadow: 2px 2px 6px rgba(0,0,0,.12);
  }
  .submenu-item {
    position: absolute; left: 28px; font-size: 12px; line-height: 16px; color: var(--white);
  }

  /* Footer */
  .footer {
    position: absolute; left: 0; top: 634px; width: 1200px; height: 32px;
    background: var(--navy); color: var(--white);
    font-size: 8.8px; line-height: 32px; text-align: center;
  }
  .footer .build { position: absolute; right: 12px; top: 0; font-size: 9px; }
</style>
</head>
<body>
  <header class="topbar">
    <div class="brand"><span class="brand-dot"></span><span class="brand-name">Yieldora</span></div>
    <div class="nav-item is-open">ADMIN<svg class="caret" width="7" height="5" viewBox="0 0 7 5"><path d="M0 0h7L3.5 4.5z" fill="#fff"/></svg></div>
    <div class="nav-item" style="left:328px">MANAGEMENT</div>
    <div class="nav-item" style="left:431px">PROPERTY SEARCH</div>
    <div class="nav-item" style="left:558px">INTEL</div>
    <div class="nav-item" style="left:615px">PLANNING<svg class="caret" style="margin-left:12px" width="7" height="5" viewBox="0 0 7 5"><path d="M0 0h7L3.5 4.5z" fill="#fff"/></svg></div>
    <div class="date">Tuesday October<span>03, 2017</span></div>
    <div class="avatar">
      <svg width="28" height="28" viewBox="0 0 28 28"><circle cx="14" cy="11" r="4" fill="#0255a3"/><path d="M7.5 20c0-3.5 3-5.5 6.5-5.5s6.5 2 6.5 5.5z" fill="#0255a3"/></svg>
    </div>
    <div class="welcome">WELCOME<strong>ADMIN</strong></div>
    <svg class="icon" style="left:1134px" width="16" height="17" viewBox="0 0 16 17"><path d="M8 1c-3 0-5 2.2-5 5v4L1 13h14l-2-3V6c0-2.8-2-5-5-5z" fill="#fff"/><circle cx="8" cy="15" r="2" fill="#fff"/></svg>
    <svg class="icon" style="left:1165px" width="19" height="17" viewBox="0 0 19 17"><path d="M7 1H2v15h5" stroke="#fff" stroke-width="2.4" fill="none"/><path d="M6 6h6V2l6 6.5-6 6.5v-4H6z" fill="#fff"/></svg>
  </header>

  <main>
    <section class="criteria">
      <div class="field" style="top:20px"></div>
      <div class="field" style="top:81px">SEARCH &nbsp;ID</div>
      <div class="field" style="top:138px">SEARCH PRODUCT</div>
      <div class="field" style="top:198px">DIVISIONS<svg class="arrow" width="11" height="6" viewBox="0 0 11 6"><path d="M0 0h11L5.5 6z" fill="#1c2a3a"/></svg></div>
      <div class="field" style="top:254px">REGIONS<svg class="arrow" width="11" height="6" viewBox="0 0 11 6"><path d="M0 0h11L5.5 6z" fill="#1c2a3a"/></svg></div>
      <div class="field" style="top:313px">AREAS<svg class="arrow" width="11" height="6" viewBox="0 0 11 6"><path d="M0 0h11L5.5 6z" fill="#1c2a3a"/></svg></div>
    </section>

    <aside class="property">
      <div class="property-head">SELECT PROPERTY</div>
      <div class="property-item first">
        <div class="property-name">HARBOR POINT HOTEL &amp; TOWERS</div>
        <div class="property-code">HPTWR</div>
      </div>
      <div class="property-item second">
        <div class="property-name">CORAL COVE HOTEL</div>
        <div class="property-code">123</div>
      </div>
    </aside>
  </main>

  <nav class="menu">
    <div class="menu-item" style="top:13px">Registration</div>
    <div class="menu-item" style="top:49px">User Access</div>
    <div class="menu-item is-active" style="top:84px;height:30px">Setup</div>
    <div class="menu-item" style="top:121px">Data Imports</div>
  </nav>
  <nav class="submenu">
    <div class="submenu-item" style="top:16px">Market Segments</div>
    <div class="submenu-item" style="top:44px">Banquet &amp; Catering</div>
    <div class="submenu-item" style="top:72px">Outlets/F&amp;B SService</div>
    <div class="submenu-item" style="top:100px">Other Income</div>
    <div class="submenu-item" style="top:128px">Impact Dates</div>
    <div class="submenu-item" style="top:156px">Inventory</div>
    <div class="submenu-item" style="top:184px">Geo/Location</div>
    <div class="submenu-item" style="top:212px">Distribution Chaneels</div>
  </nav>

  <footer class="footer">
    COPYRIGHTS @ 2017 ALL RIGHTS RESERVED
    <span class="build">X37</span>
  </footer>
</body>
</html>
```